I need a compelling, relevant cover for a book being published in January - title is the name of this project. The book is a call to action to women to become entrepreneurs as today's best path to achieving parity, purpose, prosperity and passion. See extended description of the book's message online at:
walkingtallneverwalkingalonetoday.example
(and attached pdf -- the cover art posted here is simply a placeholder/clip art ). I'm looking for something more emotional and exciting and distinctive and appropriate to the subject matter and message..
type on cover must include:
Walking Tall Never Means Walking Alone
By Marisol T. Vandeweg
How Trusting Your Instincts Can Reshape Your Days and Build Your Venture
With a Foreword by CEO Priya D. Halloran

Target Market(s)

Professional women, women business owners, aspiring women students, marketers who target women in business, such as IT providers; lenders and funders; financial services like credit card issuers -- anyone who sells to women i biz. Women's networking groups,entrepreneurship divisions at universities, and associations. International audience but tilted toward US readers.

Font styles to use
Serif

Requirements
Nice to have
• Something that stands out from the crowd -- that would make a woman want to pick up the book because it "speaks" her language/values. Something that addresses contemporary, up-to-date ideas about gender equity/sex roles/women's advancement
Should not have
• NOTHING PINK! Please avoid "empowerment" looks and ideas (too cliche) and avoid traditional business images, like briefcases

```html
<!DOCTYPE html>
<html lang="en">
<head>
<meta charset="utf-8">
<title>Walking Tall Never Means Walking Alone — Book Cover</title>
<link href="https://fonts.googleapis.com/css2?family=Roboto+Slab:wght@800;900&family=Source+Serif+4:wght@400;700&display=swap" rel="stylesheet">
<style>
  :root {
    --bg-top: #d9e0e5;
    --bg-mid: #e9edf0;
    --bg-bottom: #f1f3f5;
    --title-white: #ffffff;
    --title-shadow: rgba(38, 50, 62, 0.6);
    --accent-blue: #1b95da;
    --accent-red: #d9201a;
    --text-grey: #33373b;
    --rule-blue: #1b95da;
    --rule-red: #d9201a;
    --art-light: #e4e9ec;
    --art-mid: #c3ccd3;
  }
  * { margin: 0; padding: 0; box-sizing: border-box; }
  html, body { width: 849px; height: 1200px; overflow: hidden; }
  body { background: var(--bg-bottom); }
  .cover {
    position: relative;
    width: 849px;
    height: 1200px;
    overflow: hidden;
    background: linear-gradient(180deg, var(--bg-top) 0%, var(--bg-mid) 45%, var(--bg-bottom) 100%);
  }
  .title {
    position: absolute;
    top: 48px;
    left: 0;
    width: 100%;
    text-align: center;
    font-family: "Roboto Slab", Georgia, serif;
    font-weight: 900;
    font-size: 80px;
    line-height: 100px;
    letter-spacing: 1px;
    text-transform: uppercase;
    color: var(--title-white);
    text-shadow: 0 2px 2px var(--title-shadow), 0 4px 12px var(--title-shadow);
  }
  .title .line { display: block; }
  .title .accent-blue { color: var(--accent-blue); }
  .title .accent-red { color: var(--accent-red); }
  .balance-art {
    position: absolute;
    top: 455px;
    left: 85px;
    width: 680px;
    height: 340px;
    background: linear-gradient(180deg, var(--art-light) 0%, var(--art-mid) 100%);
    border-radius: 4px;
    opacity: 0.7;
  }
  .rule { position: absolute; height: 2px; }
  .rule-left { top: 912px; left: 0; width: 355px; background: var(--rule-blue); }
  .rule-right { top: 1042px; left: 580px; width: 269px; background: var(--rule-red); }
  .subtitle {
    position: absolute;
    top: 930px;
    left: 0;
    width: 100%;
    text-align: center;
    font-family: "Source Serif 4", Georgia, serif;
    font-weight: 400;
    font-size: 32px;
    line-height: 42px;
    color: var(--text-grey);
  }
  .author {
    position: absolute;
    top: 1060px;
    left: 0;
    width: 100%;
    text-align: center;
    font-family: "Roboto Slab", Georgia, serif;
    font-weight: 800;
    font-size: 32px;
    line-height: 40px;
    letter-spacing: 2px;
    text-transform: uppercase;
    color: var(--accent-blue);
  }
  .foreword {
    position: absolute;
    top: 1126px;
    left: 0;
    width: 100%;
    text-align: center;
    font-family: "Source Serif 4", Georgia, serif;
    font-weight: 700;
    font-size: 27px;
    line-height: 36px;
    color: var(--accent-red);
  }
</style>
</head>
<body>
  <main class="cover">
    <h1 class="title">
      <span class="line">Walking <span class="accent-blue">Tall</span></span>
      <span class="line">Never Means</span>
      <span class="line">Walking</span>
      <span class="line accent-red">Alone</span>
    </h1>

    <div class="balance-art" role="img" aria-label="Silver spheres balanced on a seesaw plank: a stack of small spheres on the left, one large sphere on the right, resting on a sphere fulcrum"></div>

    <div class="rule rule-left"></div>
    <p class="subtitle">How Trusting Your Instincts Can Reshape<br>Your Days and Build Your Venture</p>
    <div class="rule rule-right"></div>

    <p class="author">By Marisol T. Vandeweg</p>
    <p class="foreword">With a Foreword by CEO Priya D. Halloran</p>
  </main>
</body>
</html>
```